Now Leasing Banner

Looking for a banner that says the following information approx 4' x 30'

Now Leasing Maplebrook Terrace 925-318-6042

Target Market(s)

Drive by traffic

Industry/Entity Type

Residential property management

Requirements
Must have
• Clear and readable from a distance

```html
<!DOCTYPE html>
<html lang="en">
<head>
<meta charset="utf-8">
<title>Now Leasing Maplebrook Terrace</title>
<link rel="stylesheet" href="https://fonts.googleapis.com/css2?family=Anton&display=swap">
<style>
  :root {
    --banner-bg: #ffffff;
    --leaf-green: #76c043;
    --lime: #d4e021;
    --forest: #1b3f1f;
    --outline: #ffffff;
  }
  html, body {
    margin: 0;
    padding: 0;
    overflow: hidden;
    background: var(--banner-bg);
  }
  .banner {
    display: block;
    width: 1200px;
    height: 160px;
  }
  .corner-green { fill: var(--leaf-green); }
  .corner-lime { fill: var(--lime); }
  .banner-text {
    font-family: 'Anton', 'Oswald', sans-serif;
    fill: var(--forest);
    stroke: var(--outline);
    paint-order: stroke fill;
    stroke-linejoin: round;
  }
  .tagline { font-size: 68px; stroke-width: 6px; }
  .headline { font-size: 134px; stroke-width: 8px; }
  .phone { font-size: 38px; stroke-width: 4px; }
</style>
</head>
<body>
<svg class="banner" viewBox="0 0 1200 160" xmlns="http://www.w3.org/2000/svg">
  <rect width="1200" height="160" fill="var(--banner-bg)"/>

  <g class="corner corner-left">
    <polygon class="corner-lime" points="217,0 291,0 0,158"/>
    <polygon class="corner-green" points="0,0 217,0 0,158"/>
  </g>
  <g class="corner corner-right">
    <polygon class="corner-lime" points="908,0 983,0 1200,158"/>
    <polygon class="corner-green" points="983,0 1200,0 1200,158"/>
  </g>

  <text class="banner-text tagline" x="33" y="84" textLength="88" lengthAdjust="spacingAndGlyphs">NOW</text>
  <text class="banner-text headline" x="140" y="130" textLength="871" lengthAdjust="spacingAndGlyphs">LEASING MAPLEBROOK TERRACE</text>
  <text class="banner-text phone" x="1027" y="93" textLength="140" lengthAdjust="spacingAndGlyphs">925-318-6042</text>
</svg>
</body>
</html>
```